New web page, 2 companies on the one page

A new web page for an engineering consultancy and maintenance management company

Corlett & Associates is the parent company covering the design and consultancy
Valtrix Engineering is the Maintenance and Reliability company

Target Market(s)

Food & Beverage, ingredients Manufacturing
engineering managers

Coding

Coded - Design and coding required

Number of Pages Required

1 page

Font styles to use
Other font styles liked:
• Roboto

Colors
1861ab
85acd3
d0dfed
cee9f5

```html
<!DOCTYPE html>
<html lang="en">
<head>
<meta charset="utf-8">
<title>Corlett &amp; Associates</title>
<link href="https://fonts.googleapis.com/css2?family=Roboto:wght@400;500;700;900&display=swap" rel="stylesheet">
<style>
:root{
  --blue-deep:#1861ab;
  --blue-mid:#85acd3;
  --blue-btn:#6e9acf;
  --blue-card:#b1c6df;
  --blue-pale:#d0dfed;
  --ink:#111;
  --text:#222;
  --white:#fff;
  --black:#000;
}
*{margin:0;padding:0;box-sizing:border-box}
html,body{width:1200px;height:2889px;overflow:hidden;background:var(--white)}
body{font-family:'Roboto',sans-serif;color:var(--text)}
.page{position:relative;width:1200px;height:2889px;overflow:hidden}
.abs{position:absolute}

/* hero */
.hero-shape{position:absolute;left:0;top:0}
.brand{position:absolute;left:115px;top:38px;display:flex;align-items:center;gap:10px;color:var(--white);font-weight:700;font-size:22px;letter-spacing:.5px}
.brand-mark{width:30px;height:30px;background:var(--blue-mid)}
.nav{position:absolute;top:45px;left:389px;display:flex;gap:0;font-weight:700;font-size:15.5px;color:var(--white)}
.nav a{color:var(--white);text-decoration:none;position:absolute;white-space:nowrap}
.nav-active{position:absolute;left:388px;top:106px;width:40px;height:3px;background:var(--blue-mid)}
.btn{display:flex;align-items:center;justify-content:center;background:var(--blue-btn);color:var(--white);font-weight:700;font-size:15.5px;text-decoration:none}
.quote-btn{position:absolute;left:920px;top:31px;width:168px;height:48px}
.hero-title{position:absolute;left:110px;top:224px;font-size:45px;font-weight:700;color:var(--white);letter-spacing:.5px}
.hero-text{position:absolute;left:115px;top:282px;width:480px;font-size:16px;line-height:24px;color:var(--white)}
.hero-btn{position:absolute;left:113px;top:350px;width:134px;height:48px}
.dots{position:absolute;display:flex;gap:8px}
.dots span{display:block;width:20px;height:3px;background:#555}
.dots span.on{background:var(--white)}

/* about */
.about-img{position:absolute;left:123px;top:718px}
.section-title{font-size:38px;font-weight:700;color:var(--ink);letter-spacing:.3px}
.about-title{position:absolute;left:675px;top:772px}
.about-text{position:absolute;left:675px;top:832px;width:445px;font-size:16px;line-height:30px;color:var(--text)}
.about-btn{position:absolute;left:675px;top:1093px;width:134px;height:49px}

/* services */
.services-title{position:absolute;left:0;width:1200px;text-align:center;top:1285px}
.card{position:absolute;top:1382px;width:313px;height:457px;background:var(--blue-card);text-align:center;padding:33px 22px 0}
.card-icon{width:74px;height:73px;background:var(--white);margin:0 auto;display:flex;align-items:center;justify-content:center}
.card-title{margin-top:30px;font-size:18.5px;font-weight:700;line-height:30px;color:var(--ink)}
.card-text{margin-top:6px;font-size:16px;line-height:26px;color:var(--text)}
.card-more{position:absolute;left:0;width:100%;top:1690px;font-size:15.5px;font-weight:700;color:var(--white);display:flex;justify-content:center;align-items:center;gap:6px}
.card-photo{position:absolute;top:1737px;width:247px;height:148px}
.svc-dots{left:1044px;top:1921px}
.svc-dots span{background:#444}
.svc-dots span.on{background:var(--blue-btn)}

/* reviews */
.reviews-title{position:absolute;left:0;width:1200px;text-align:center;top:2002px}
.quote-mark{position:absolute;left:205px;top:2066px}
.quote{position:absolute;left:240px;width:720px;top:2082px;text-align:center;font-size:25px;font-weight:700;line-height:30px;color:var(--ink)}
.rev-nav{position:absolute;top:2218px;font-size:15px;color:var(--text);display:flex;align-items:center;gap:8px}
.avatar{position:absolute;border-radius:50%}
.reviewer{position:absolute;left:0;width:1200px;top:2281px;text-align:center;color:var(--blue-btn);font-weight:700;font-size:15.5px}

/* footer */
.footer-brand{position:absolute;left:112px;top:2568px;display:flex;align-items:center;gap:10px;color:var(--white);font-size:28px;font-weight:700;letter-spacing:1px}
.footer-about{position:absolute;left:114px;top:2636px;width:260px;font-size:16px;line-height:26px;color:var(--white)}
.f-head{position:absolute;top:2550px;font-size:18px;font-weight:700;color:var(--white)}
.f-links{position:absolute;left:468px;top:2586px;list-style:none;font-size:16px;line-height:30.3px;color:var(--white)}
.f-contact{position:absolute;left:655px;top:2586px;font-size:16px;color:var(--white)}
.f-contact .row{display:flex;gap:8px;align-items:flex-start;position:absolute;left:0;white-space:nowrap;line-height:26px}
.social{position:absolute;top:2579px;display:flex;gap:8px;left:912px}
.social span{width:35px;height:35px;border-radius:50%;background:var(--blue-btn);display:block}
.f-rule{position:absolute;left:111px;top:2788px;width:978px;height:1px;background:#262626}
.copyright{position:absolute;left:0;width:1200px;top:2824px;text-align:center;font-size:15.5px;color:var(--white)}
</style>
</head>
<body>
<div class="page">

  <!-- HERO -->
  <svg class="hero-shape" width="1200" height="640" viewBox="0 0 1200 640" role="img" aria-label="Evening photograph of a harbour city skyline with a bridge and moored sailboats">
    <defs>
      <linearGradient id="heroSky" x1="0" y1="0" x2="0" y2="1">
        <stop offset="0" stop-color="#3a3f6a"/>
        <stop offset=".28" stop-color="#6b5a70"/>
        <stop offset=".5" stop-color="#3b4a5e"/>
        <stop offset=".8" stop-color="#2c4258"/>
        <stop offset="1" stop-color="#1d2c3a"/>
      </linearGradient>
    </defs>
    <polygon points="0,510 600,628 1200,510 1200,520 600,610 0,520" fill="#6e9acf"/>
    <polygon points="0,0 1200,0 1200,510 600,612 0,510" fill="url(#heroSky)"/>
  </svg>

  <div class="brand"><span class="brand-mark"></span>CORLETT</div>
  <nav class="nav">
    <a style="left:0">HOME</a>
    <a style="left:75px">ABOUT US</a>
    <a style="left:183px">REVIEWS</a>
    <a style="left:283px">CONTACT US</a>
    <a style="left:428px;display:flex;align-items:center;gap:8px;top:2px">
      <svg width="12" height="13" viewBox="0 0 12 13"><circle cx="6" cy="3.5" r="3" fill="#fff"/><path d="M0 13c0-4 2.5-6 6-6s6 2 6 6z" fill="#fff"/></svg>LOGIN</a>
  </nav>
  <div class="nav-active"></div>
  <a class="btn quote-btn">REQUEST A QUOTE</a>

  <h1 class="hero-title">CORLETT ASSOCIATES</h1>
  <p class="hero-text">Lorem ipsum dolor sit amet, consectetur adipiscing elit, sed do eius­mod tempor incididunt ut labore et dolore magna aliqua.</p>
  <a class="btn hero-btn">LEARN MORE</a>
  <div class="dots" style="left:579px;top:521px"><span class="on"></span><span style="background:#6b7785;width:12px"></span></div>

  <!-- ABOUT -->
  <svg class="about-img" width="460" height="482" viewBox="0 0 460 482" role="img" aria-label="Photograph of a business team meeting around a conference table">
    <defs>
      <linearGradient id="aboutPhoto" x1="0" y1="0" x2="1" y2="1">
        <stop offset="0" stop-color="#8fa2bd"/>
        <stop offset=".5" stop-color="#3e4d66"/>
        <stop offset="1" stop-color="#1f2a3d"/>
      </linearGradient>
    </defs>
    <polygon points="230,0 455,110 455,372 230,482 5,372 5,110" fill="url(#aboutPhoto)"/>
  </svg>
  <h2 class="section-title about-title">ABOUT US</h2>
  <p class="about-text">Corlett &amp; Associates is specialised manufacturing engineering support organisation that can provide fast, nimble, and flexible services. We have a proven track record in delivering tangible outcomes in process design and fit-out, project management, manufacturing process and maintenance design and execu­tion. Our specialist focus in food manufacturing across a range of sectors allows our team to deliver real benefits to perfor­mance and recognition of the clients investment</p>
  <a class="btn about-btn">LEARN MORE</a>

  <!-- SERVICES -->
  <h2 class="section-title services-title">OUR SERVICES</h2>

  <div class="card" style="left:2px">
    <div class="card-icon" role="img" aria-label="Line icon of a factory building with a gear"></div>
    <h3 class="card-title">PROCESS &amp; FACILITIES DESIGN</h3>
    <p class="card-text">Lorem ipsum dolor sit amet, consecte­tur adipiscing elit, sed do eiusmod tempor incididunt ut labore et dolore magna aliqua.</p>
  </div>
  <div class="card" style="left:333px">
    <div class="card-icon" role="img" aria-label="Line icon of a document with a gear and pencil"></div>
    <h3 class="card-title">PROJECT MANAGEMENT</h3>
    <p class="card-text">Lorem ipsum dolor sit amet, consecte­tur adipiscing elit, sed do eiusmod tempor incididunt ut labore et dolore magna aliqua.</p>
  </div>
  <div class="card" style="left:664px">
    <div class="card-icon" role="img" aria-label="Line icon of a head with circuit lines"></div>
    <h3 class="card-title">MAJOR EQUIPMENT AND SERVICES INSTALLATION &amp; COMMISSIONING.</h3>
    <p class="card-text">Lorem ipsum dolor sit amet, consecte­tur adipiscing elit.</p>
  </div>
  <div class="card" style="left:995px">
    <div class="card-icon" role="img" aria-label="Line icon of an engineer with a robotic arm"></div>
    <h3 class="card-title">ENGINEERING &amp; MAINTENANCE MANAGEMENT</h3>
    <p class="card-text">Lorem ipsum dolor sit amet, consecte­tur adipiscing elit, sed do eiusmod tempor incididunt ut labore</p>
  </div>

  <div class="card-more" style="left:2px;width:313px">LEARN MORE <svg width="13" height="13" viewBox="0 0 13 13"><circle cx="6.5" cy="6.5" r="6.5" fill="#fff"/><path d="M4 6.5h5M6.5 4l2.5 2.5L6.5 9" stroke="#b1c6df" stroke-width="1.6" fill="none"/></svg></div>
  <div class="card-more" style="left:333px;width:313px">LEARN MORE <svg width="13" height="13" viewBox="0 0 13 13"><circle cx="6.5" cy="6.5" r="6.5" fill="#fff"/><path d="M4 6.5h5M6.5 4l2.5 2.5L6.5 9" stroke="#b1c6df" stroke-width="1.6" fill="none"/></svg></div>
  <div class="card-more" style="left:664px;width:313px">LEARN MORE <svg width="13" height="13" viewBox="0 0 13 13"><circle cx="6.5" cy="6.5" r="6.5" fill="#fff"/><path d="M4 6.5h5M6.5 4l2.5 2.5L6.5 9" stroke="#b1c6df" stroke-width="1.6" fill="none"/></svg></div>
  <div class="card-more" style="left:995px;width:313px">LEARN MORE <svg width="13" height="13" viewBox="0 0 13 13"><circle cx="6.5" cy="6.5" r="6.5" fill="#fff"/><path d="M4 6.5h5M6.5 4l2.5 2.5L6.5 9" stroke="#b1c6df" stroke-width="1.6" fill="none"/></svg></div>

  <div class="card-photo" style="left:35px;background:linear-gradient(135deg,#2b3d5a,#6d7f99 60%,#c9d0da)" role="img" aria-label="Photograph of hands reviewing engineering drawings on a table"></div>
  <div class="card-photo" style="left:366px;background:linear-gradient(135deg,#c9b9a3,#efe9e0 55%,#8da7c7)" role="img" aria-label="Photograph of a team reviewing charts on a laptop"></div>
  <div class="card-photo" style="left:697px;background:linear-gradient(135deg,#5b4a3a,#c9a24a 45%,#3a3a3a)" role="img" aria-label="Photograph of a worker in a hard hat at an industrial site"></div>
  <div class="card-photo" style="left:1028px;background:linear-gradient(135deg,#5e6f82,#b9c3cf 55%,#eef1f4)" role="img" aria-label="Photograph of an engineer using a laptop beside factory machinery"></div>

  <div class="dots svc-dots"><span class="on"></span><span style="width:12px"></span></div>

  <!-- REVIEWS -->
  <h2 class="section-title reviews-title">OUR REVIEWS</h2>
  <svg class="quote-mark" width="33" height="27" viewBox="0 0 33 27"><path d="M0 27V12C0 5 4 1 11 0v5c-3 1-4 3-4 6h6v16zM18 27V12c0-7 4-11 11-12v5c-3 1-4 3-4 6h6v16z" fill="#6e9acf"/></svg>
  <p class="quote">Lorem ipsum dolor sit amet, consectetur adipiscing elit, sed do eiusmod tempor incididunt ut labore et dolore magna aliqua. Quis ipsum suspendisse ultrices gravida.</p>

  <div class="rev-nav" style="left:437px"><svg width="16" height="8" viewBox="0 0 16 8"><path d="M0 4l5-4v3h11v2H5v3z" fill="#111"/></svg>Pre /</div>
  <div class="avatar" role="img" aria-label="Portrait photo of a reviewer" style="left:504px;top:2204px;width:47px;height:47px;background:radial-gradient(circle,#c9b7a6,#8e7d70)"></div>
  <div class="avatar" style="left:570px;top:2197px;width:61px;height:61px;border:3px solid #6e9acf;background:#fff"></div>
  <div class="avatar" role="img" aria-label="Portrait photo of the featured reviewer" style="left:577px;top:2204px;width:47px;height:47px;background:radial-gradient(circle,#b3b7bf,#3b4250)"></div>
  <div class="avatar" role="img" aria-label="Portrait photo of a reviewer" style="left:650px;top:2204px;width:47px;height:47px;background:radial-gradient(circle,#d7c2b4,#5a4a44)"></div>
  <div class="rev-nav" style="left:727px">Next <svg width="16" height="8" viewBox="0 0 16 8"><path d="M16 4l-5-4v3H0v2h11v3z" fill="#111"/></svg></div>
  <p class="reviewer">Marcus</p>

  <!-- FOOTER -->
  <svg class="abs" style="left:0;top:2380px" width="1200" height="509" viewBox="0 0 1200 509">
    <polygon points="0,98 600,6 1200,98" fill="#6e9acf"/>
    <polygon points="0,98 600,20 1200,98 1200,509 0,509" fill="#000"/>
  </svg>

  <div class="footer-brand"><span class="brand-mark" style="width:34px;height:34px"></span>VALTRIX</div>
  <p class="footer-about">Lorem ipsum dolor sit amet, consec­tetur adipiscing elit, sed do eiusmod tempor incididunt ut labore et dolore magna aliqua.</p>

  <h4 class="f-head" style="left:466px">QUICK LINK</h4>
  <ul class="f-links">
    <li>Home</li><li>About Us</li><li>Reviews</li><li>Contact Us</li>
  </ul>

  <h4 class="f-head" style="left:655px">CONTACT</h4>
  <div class="f-contact">
    <div class="row" style="top:0"><svg width="10" height="14" viewBox="0 0 10 14" style="margin-top:6px"><path d="M5 0a5 5 0 0 1 5 5c0 4-5 9-5 9S0 9 0 5a5 5 0 0 1 5-5z" fill="#fff"/><circle cx="5" cy="5" r="2" fill="#000"/></svg><span>Lorem ipsum dolor<br>sit amet</span></div>
    <div class="row" style="top:61px"><svg width="13" height="13" viewBox="0 0 13 13" style="margin-top:6px"><path d="M3 0l2 3-1.5 1.5a8 8 0 0 0 5 5L10 8l3 2-1.5 3C6 13 0 7 0 1.5z" fill="#fff"/></svg><span>155-010-4420</span></div>
    <div class="row" style="top:101px"><svg width="14" height="11" viewBox="0 0 14 11" style="margin-top:8px"><rect x=".75" y=".75" width="12.5" height="9.5" fill="none" stroke="#fff" stroke-width="1.5"/><path d="M1 1l6 5 6-5" fill="none" stroke="#fff" stroke-width="1.5"/></svg><span>hello@corlettassociates.example</span></div>
  </div>

  <h4 class="f-head" style="left:914px">FOLLOW US</h4>
  <div class="social" aria-label="Social media links"><span></span><span></span><span></span></div>

  <div class="f-rule"></div>
  <p class="copyright">© 2021 Corlett Associates All Rights Reserved</p>
</div>
</body>
</html>
```